Shopify Web-Page "Tiny-ThreadDays

We are building a new business in Switzerland offering premium sewing holiday camps for kids aged 9–14. In enclosed brief outlines our requirements for a complete Shopify homepage design and a multilingual logo creation.
Domains: tiny-threaddays.ch ; tiny-giornifilo.ch ; tiny-fadentage.ch

Project Overview
We are looking for:
1. A modern, fully designed Shopify homepage in English using standard Shopify content blocks (no custom coding), which we can later update ourselves. Supporting Multilanguage (EN, German, Italian).

2. A logo design that includes the brand identity and communicates our multilingual, creative, and child-focused positioning.

All details in enclosed

```html
<!DOCTYPE html>
<html lang="en">
<head>
<meta charset="utf-8">
<title>Tiny-ThreadDays – Premium Sewing Holiday Camps</title>
<link href="https://fonts.googleapis.com/css2?family=Poppins:wght@400;500;600;700;800&family=Nunito+Sans:wght@400;600;700&display=swap" rel="stylesheet">
<style>
:root{
  --pink:#e8457f;
  --pink-soft:#fde3ec;
  --blue:#2aa4d8;
  --blue-soft:#eaf6fc;
  --navy:#13204a;
  --yellow:#f5b622;
  --ink:#1e2433;
  --muted:#6b7280;
  --line:#e6e9ef;
  --white:#ffffff;
}
*{box-sizing:border-box;margin:0;padding:0}
html,body{width:1200px;height:4904px;overflow:hidden}
body{font-family:"Nunito Sans",Arial,sans-serif;color:var(--ink);background:var(--white);position:relative}
h1,h2,h3,h4,.brand{font-family:"Poppins",Arial,sans-serif}
.accent{color:var(--pink)}
.underline{color:var(--pink);border-bottom:3px solid var(--yellow)}
.btn{display:inline-flex;align-items:center;gap:8px;background:var(--blue);color:#fff;font:600 13px "Poppins",sans-serif;padding:11px 22px;border-radius:24px}
.btn-pink{background:var(--pink)}
.eyebrow{font:700 12px "Poppins",sans-serif;letter-spacing:1.5px;color:var(--blue);text-transform:uppercase;text-align:center}
.section-title{font:800 30px "Poppins",sans-serif;text-align:center;text-transform:uppercase;margin-top:8px}
.ph{display:block}

/* header */
.site-header{position:absolute;top:0;left:0;width:1200px;height:72px;background:#fff;display:flex;align-items:center;padding:0 60px;z-index:3}
.brand{font-weight:800;font-size:22px;color:var(--pink);display:flex;align-items:center;gap:10px}
.brand-dot{width:14px;height:14px;border-radius:50%;background:var(--yellow)}
.main-nav{display:flex;gap:26px;margin-left:150px;font:500 13px "Poppins",sans-serif}
.main-nav .active{color:var(--pink);border-bottom:2px solid var(--pink);padding-bottom:3px}
.header-tools{margin-left:auto;display:flex;align-items:center;gap:22px;font:500 13px "Poppins",sans-serif}
.lang{display:flex;align-items:center;gap:6px}
.lang i{width:16px;height:16px;border-radius:50%;background:var(--blue);display:inline-block}

/* hero */
.hero{position:absolute;top:72px;left:0;width:1200px;height:560px;background:linear-gradient(100deg,#5a3a34 0%,#9b6a55 40%,#d8a57c 70%,#e9c7a3 100%);overflow:hidden}
.hero-copy{position:absolute;left:60px;top:60px;width:460px;color:#fff}
.hero-copy h1{font-size:42px;line-height:1.12;font-weight:800;text-transform:uppercase}
.hero-copy p{font-size:14px;line-height:1.6;margin:18px 0 26px;color:#fdf3ec}
.hero-join{display:flex;align-items:center;gap:10px;margin-top:30px;font-size:13px}
.avatars{display:flex}
.avatars span{width:28px;height:28px;border-radius:50%;border:2px solid #fff;margin-left:-8px;background:#f2c9a8}
.avatars span:first-child{margin-left:0;background:#c99679}
.avatars span:nth-child(2){background:#e6b090}
.hero-wave{position:absolute;left:0;bottom:0}

/* about */
.about{position:absolute;top:632px;left:0;width:1200px;height:620px}
.collage{position:absolute;left:150px;top:40px;width:380px;height:380px;border-radius:50%;overflow:hidden;display:grid;grid-template-columns:1fr 1fr;gap:8px;background:#fff}
.collage div:nth-child(1){background:linear-gradient(135deg,#c9d7e6,#8aa1bd)}
.collage div:nth-child(2){background:linear-gradient(135deg,#e8d3bf,#c59b7a)}
.collage div:nth-child(3){background:linear-gradient(135deg,#d7c7b0,#a68768)}
.collage div:nth-child(4){background:linear-gradient(135deg,#f3d5d9,#d69aa4)}
.collage-ring{position:absolute;left:130px;top:20px}
.collage-core{position:absolute;left:300px;top:170px;width:80px;height:80px;border-radius:50%;background:#fff;box-shadow:0 4px 14px rgba(0,0,0,.12)}
.about-text{position:absolute;left:600px;top:60px;width:540px}
.about-text .eyebrow{text-align:left}
.about-text h2{font-size:26px;font-weight:800;text-transform:uppercase;margin:8px 0 18px}
.about-text p{font-size:13px;line-height:1.7;color:var(--muted);margin-bottom:12px}
.team{display:flex;gap:60px;margin-top:22px}
.member{display:flex;align-items:center;gap:12px}
.member .ph{width:48px;height:48px;border-radius:50%;background:linear-gradient(135deg,#e7c3a8,#b88a6c)}
.member b{display:block;font:600 14px "Poppins",sans-serif}
.member small{font-size:12px;color:var(--muted)}

/* how */
.how{position:absolute;top:1252px;left:0;width:1200px;height:460px}
.how-bg{position:absolute;left:0;top:0}
.how-inner{position:absolute;top:90px;left:0;width:1200px}
.steps{display:flex;gap:18px;justify-content:center;margin-top:30px}
.step{width:190px;height:150px;background:#fff;border-radius:10px;padding:16px;box-shadow:0 6px 18px rgba(30,60,110,.08);position:relative}
.step .num{position:absolute;right:14px;top:10px;font:800 34px "Poppins",sans-serif;color:#eef1f5}
.step .icon{width:30px;height:30px;border-radius:8px;background:var(--pink-soft);margin-bottom:12px}
.step h4{font-size:13px;font-weight:600;margin-bottom:6px}
.step p{font-size:11px;line-height:1.5;color:var(--muted)}

/* why */
.why{position:absolute;top:1712px;left:0;width:1200px;height:660px}
.why .eyebrow{margin-top:20px}
.why-logo{position:absolute;left:460px;top:200px;width:280px;height:280px;border-radius:50%;border:10px solid var(--blue-soft);background:#fff;display:flex;align-items:center;justify-content:center}
.why-logo .brand{font-size:24px}
.feature{position:absolute;display:flex;align-items:center;gap:18px;font-size:14px;line-height:1.5;width:340px}
.feature .ico{flex:none;width:60px;height:60px;border-radius:50%;display:flex;align-items:center;justify-content:center}
.feature.left{justify-content:flex-end;text-align:right}
.ico.y{background:var(--yellow)}.ico.b{background:var(--blue)}.ico.p{background:var(--pink)}

/* camps */
.camps{position:absolute;top:2392px;left:0;width:1200px;height:620px}
.camp-list{display:flex;gap:30px;justify-content:center;margin-top:30px}
.camp{width:290px;border-radius:10px;background:#fff;box-shadow:0 6px 20px rgba(30,40,70,.1);overflow:hidden}
.camp .ph{height:170px}
.camp-body{padding:16px}
.camp h4{font-size:15px;font-weight:600;margin-bottom:6px}
.camp p{font-size:11px;line-height:1.5;color:var(--muted);margin-bottom:12px}
.meta{display:grid;grid-template-columns:1fr 1fr;gap:8px 10px;font-size:11px;border-top:1px solid var(--line);padding-top:10px}
.meta b{font-weight:700;margin-right:8px}
.camps .center{text-align:center;margin-top:30px}

/* cta */
.cta{position:absolute;top:3012px;left:0;width:1200px;height:440px}
.cta-inner{position:absolute;top:150px;width:1200px;text-align:center;color:#fff}
.cta h2{font-size:34px;font-weight:800;text-transform:uppercase}
.cta p{font-size:14px;margin:12px auto 20px;width:640px;line-height:1.6}
.cta .btn{background:#fff;color:var(--blue)}

/* faq */
.faq{position:absolute;top:3470px;left:0;width:1200px;height:980px}
.faq-list{width:880px;margin:34px auto 0;display:flex;flex-direction:column;gap:14px}
.faq-item{border:1px solid var(--line);border-radius:6px;padding:0 22px;height:56px;display:flex;align-items:center;justify-content:space-between;font:500 14px "Poppins",sans-serif}
.faq-item.open{height:112px;flex-direction:column;align-items:stretch;justify-content:center;border-color:var(--pink);border-left:4px solid var(--pink)}
.faq-item.open .q{display:flex;justify-content:space-between}
.faq-item.open p{font:400 12px "Nunito Sans",sans-serif;color:var(--muted);margin-top:8px;line-height:1.5}
.chev{color:var(--muted);font-size:12px}
.to-top{position:absolute;left:1100px;top:4370px;width:40px;height:40px;border-radius:50%;background:var(--pink);display:flex;align-items:center;justify-content:center}

/* footer */
.site-footer{position:absolute;top:4464px;left:0;width:1200px;height:440px;background:var(--navy);color:#cfd6e6}
.footer-cols{position:absolute;top:70px;left:80px;right:80px;display:flex}
.footer-cols h4{color:var(--pink);font-size:15px;font-weight:600;margin-bottom:16px}
.col-brand{width:280px}
.col-brand .brand{font-size:26px}
.follow{display:flex;align-items:center;gap:8px;margin-top:120px;font-size:13px}
.follow i{width:26px;height:26px;border-radius:50%;background:var(--blue);display:inline-block}
.col-links{width:200px}
.col-links li,.col-contact li{list-style:none;font-size:13px;margin-bottom:10px}
.col-contact{width:260px}
.col-contact li{display:flex;gap:10px;align-items:flex-start}
.col-contact li i{flex:none;width:22px;height:22px;border-radius:50%;background:var(--pink);display:inline-block}
.col-news{width:300px}
.col-news p{font-size:13px;line-height:1.6;margin-bottom:16px}
.news-field{display:flex;background:#fff;border-radius:24px;padding:4px;width:280px}
.news-field span{flex:1;color:#9aa3b5;font-size:12px;padding:8px 14px}
.news-field b{width:34px;height:34px;border-radius:50%;background:var(--pink)}
.copyright{position:absolute;left:80px;right:80px;bottom:0;height:56px;border-top:1px solid rgba(255,255,255,.15);text-align:center;font-size:12px;line-height:56px}
</style>
</head>
<body>

<header class="site-header">
  <div class="brand"><span class="brand-dot"></span>Tiny-ThreadDays</div>
  <nav class="main-nav">
    <span class="active">Home</span><span>About Us</span><span>Camps</span><span>How It Works</span><span>FAQs</span><span>Contact</span>
  </nav>
  <div class="header-tools">
    <span class="lang"><i></i>English ▾</span>
    <span class="btn btn-pink">Contact Us</span>
  </div>
</header>

<section class="hero">
  <div class="ph" role="img" aria-label="Photo of children sewing at a workshop table" style="position:absolute;inset:0"></div>
  <div class="hero-copy">
    <h1>Premium Sewing<br><span class="accent">Holiday Camps For</span><br>Kids 9-14</h1>
    <p>Creative fun in Zurich – Multilingual and Inspiring! Learn sewing, build confidence, and create unique fashion pieces in our small group camps.</p>
    <span class="btn">View Upcoming Camps →</span>
    <div class="hero-join"><span class="avatars"><span></span><span></span><span></span></span>Join 200+ happy campers!</div>
  </div>
  <svg class="hero-wave" width="1200" height="90" viewBox="0 0 1200 90"><path d="M0 60 C250 10 450 100 700 55 S1050 20 1200 50 L1200 90 L0 90Z" fill="#fff"/></svg>
</section>

<section class="about">
  <svg class="collage-ring" width="420" height="420" viewBox="0 0 420 420"><path d="M40 210 A170 170 0 0 1 210 40" fill="none" stroke="#f5b622" stroke-width="10" stroke-linecap="round"/><path d="M380 210 A170 170 0 0 1 210 380" fill="none" stroke="#2aa4d8" stroke-width="10" stroke-linecap="round"/></svg>
  <div class="collage">
    <div role="img" aria-label="Photo of a child at a sewing machine"></div>
    <div role="img" aria-label="Photo of fabric being cut"></div>
    <div role="img" aria-label="Photo of kids choosing fabrics"></div>
    <div role="img" aria-label="Photo of a finished garment"></div>
  </div>
  <div class="collage-core"></div>
  <div class="about-text">
    <div class="eyebrow">About Our Camps</div>
    <h2>Learning With Fun &amp; <span class="underline">Structure</span></h2>
    <p>At Tiny-ThreadDays, we believe in nurturing creativity while having fun. Our experienced instructors create a safe, inspiring environment where children can explore their creative potential.</p>
    <p>With over 15 years of experience in teaching children sewing, tailoring, and design, our team guides young talents through a creative week of vacation – with real results, self-sewn pieces, new friends, and lots of pride.</p>
    <p>At the last day, the children show off their success: their own sewn unique pieces, in a sympathetic fashion show.</p>
    <div class="team">
      <div class="member"><span class="ph" role="img" aria-label="Portrait of instructor Livia"></span><div><b>Livia</b><small>Sewing Expert</small></div></div>
      <div class="member"><span class="ph" role="img" aria-label="Portrait of instructor Nora"></span><div><b>Nora</b><small>Design Specialist</small></div></div>
    </div>
  </div>
</section>

<section class="how">
  <svg class="how-bg" width="1200" height="460" viewBox="0 0 1200 460"><path d="M0 40 C300 0 500 70 800 30 S1100 10 1200 35 L1200 420 C900 460 600 390 300 430 S50 440 0 420Z" fill="#eaf6fc"/></svg>
  <div class="how-inner">
    <div class="eyebrow">How Our Camps Work</div>
    <h2 class="section-title">Creative Holiday Camps For Young <span class="accent">Sewing Champs!</span></h2>
    <div class="steps">
      <div class="step"><span class="num">01</span><div class="icon"></div><h4>Project Selection</h4><p>Your child chooses their own model based on previously produced clothing items and sewing patterns.</p></div>
      <div class="step"><span class="num">02</span><div class="icon"></div><h4>Fabric selection</h4><p>High-quality fabrics are available.</p></div>
      <div class="step"><span class="num">03</span><div class="icon"></div><h4>Sewing machine</h4><p>Learn how to use a sewing machine.</p></div>
      <div class="step"><span class="num">04</span><div class="icon"></div><h4>Sewing &amp; refining</h4><p>Step by step to the goal with professional guidance.</p></div>
      <div class="step"><span class="num">05</span><div class="icon"></div><h4>Showtime!</h4><p>Fashion show in pieces worn at the end of the week.</p></div>
    </div>
  </div>
</section>

<section class="why">
  <div class="eyebrow">Why Parents Choose Us</div>
  <h2 class="section-title">Why Families Love Tiny-ThreadDays <span class="accent">Camps</span></h2>
  <div class="why-logo"><div class="brand">Tiny-ThreadDays</div></div>
  <div class="feature left" style="left:100px;top:220px">Small groups &amp; personalized attention<span class="ico y"><svg width="26" height="26" viewBox="0 0 24 24" fill="#fff"><circle cx="8" cy="8" r="3.5"/><circle cx="16" cy="8" r="3.5"/><path d="M2 20c0-4 3-6 6-6s6 2 6 6zM10 20c0-4 3-6 6-6s6 2 6 6z"/></svg></span></div>
  <div class="feature left" style="left:100px;top:320px">Multilingual supervision (DE / EN / IT)<span class="ico b"><svg width="26" height="26" viewBox="0 0 24 24" fill="none" stroke="#fff" stroke-width="2"><path d="M3 5h10M8 3v2M5 5c1 4 4 7 7 8M11 5c-1 4-4 7-7 8M13 21l4-10 4 10M14.5 17h5"/></svg></span></div>
  <div class="feature left" style="left:100px;top:420px">Pick-up Service from the Main Station<span class="ico p"><svg width="24" height="24" viewBox="0 0 24 24" fill="#fff"><path d="M12 2a7 7 0 0 0-7 7c0 5 7 13 7 13s7-8 7-13a7 7 0 0 0-7-7zm0 9.5a2.5 2.5 0 1 1 0-5 2.5 2.5 0 0 1 0 5z"/></svg></span></div>
  <div class="feature" style="left:760px;top:220px"><span class="ico y"><svg width="24" height="24" viewBox="0 0 24 24" fill="#fff"><path d="M12 2l3 7h7l-5.5 4.5L18 21l-6-4-6 4 1.5-7.5L2 9h7z"/></svg></span>Encouragement of creativity, self-confidence, and fine motor skills</div>
  <div class="feature" style="left:760px;top:320px"><span class="ico b"><svg width="24" height="24" viewBox="0 0 24 24" fill="#fff"><path d="M3 11L12 3l9 8v10h-6v-6H9v6H3z"/></svg></span>Safe, loving environment in Zurich, various places easy to reach</div>
  <div class="feature" style="left:760px;top:420px"><span class="ico p"><svg width="24" height="24" viewBox="0 0 24 24" fill="none" stroke="#fff" stroke-width="2.5"><path d="M5 12l5 5 9-10"/></svg></span>High-quality fabrics &amp; top-quality sewing machines (Veloria)</div>
</section>

<section class="camps">
  <div class="eyebrow">Our Upcoming Camps</div>
  <h2 class="section-title">Multilingual Creativity, Made Just <span class="accent">For Kids</span></h2>
  <div class="camp-list">
    <article class="camp"><div class="ph" role="img" aria-label="Photo of children at a spring sewing class" style="background:linear-gradient(135deg,#cfe0ea,#a2b7c6)"></div>
      <div class="camp-body"><h4>Spring Sewing Camp</h4><p>Join us for a creative week during spring break. Children will learn sewing basics and create their own spring-themed projects.</p>
      <div class="meta"><span><b>Age:</b>09 to 14</span><span><b>Total:</b>200 Kids</span><span><b>Date:</b>07.02.2025</span><span><b>Duration:</b>08 Days</span></div></div></article>
    <article class="camp"><div class="ph" role="img" aria-label="Photo of children outdoors at a summer camp" style="background:linear-gradient(135deg,#cfe3b6,#8fb476)"></div>
      <div class="camp-body"><h4>Summer Fashion Camp</h4><p>Our popular summer program where kids design and create their own summer wardrobe items in a fun, supportive environment.</p>
      <div class="meta"><span><b>Age:</b>09 to 14</span><span><b>Total:</b>200 Kids</span><span><b>Date:</b>07.02.2025</span><span><b>Duration:</b>08 Days</span></div></div></article>
    <article class="camp"><div class="ph" role="img" aria-label="Photo of children crafting in an autumn workshop" style="background:linear-gradient(135deg,#ecd2bd,#c59676)"></div>
      <div class="camp-body"><h4>Autumn Creative Camp</h4><p>Get ready for cooler weather by creating cozy autumn accessories and clothing items in this creative camp.</p>
      <div class="meta"><span><b>Age:</b>09 to 14</span><span><b>Total:</b>200 Kids</span><span><b>Date:</b>07.02.2025</span><span><b>Duration:</b>08 Days</span></div></div></article>
  </div>
  <div class="center"><span class="btn btn-pink">View All Camps →</span></div>
</section>

<section class="cta">
  <svg width="1200" height="440" viewBox="0 0 1200 440" style="position:absolute;left:0;top:0"><path d="M0 80 C200 20 350 110 600 60 S1000 0 1200 70 L1200 380 C1000 440 800 360 600 400 S200 440 0 380Z" fill="#2aa4d8"/></svg>
  <div class="cta-inner">
    <h2>Ready For A Creative Adventure?</h2>
    <p>Spaces are limited to 8 children per camp to ensure personalized attention. Book now to secure your child's spot!</p>
    <span class="btn">View All Camps →</span>
  </div>
</section>

<section class="faq">
  <div class="eyebrow">Frequently Asked Questions</div>
  <h2 class="section-title">Everything You Need To Know About <span class="accent">Our Camps</span></h2>
  <div class="faq-list">
    <div class="faq-item open"><div class="q"><span>Does my child need any prior knowledge?</span><span class="chev">▲</span></div>
      <p>We welcome children aged 9–14 years. This age range ensures that participants have the fine motor skills needed for sewing while still being excited about creative projects.</p></div>
    <div class="faq-item"><span>How does the pick-up service work?</span><span class="chev">▼</span></div>
    <div class="faq-item"><span>How many items of clothing are produced?</span><span class="chev">▼</span></div>
    <div class="faq-item"><span>What should my child bring to camp?</span><span class="chev">▼</span></div>
    <div class="faq-item"><span>What are the camp hours?</span><span class="chev">▼</span></div>
    <div class="faq-item"><span>We offer pick-up from Zurich Main Station at times. Parents can arrange this during booking</span><span class="chev">▼</span></div>
    <div class="faq-item"><span>What is your cancellation policy?</span><span class="chev">▼</span></div>
    <div class="faq-item"><span>How many items of clothing are produced?</span><span class="chev">▼</span></div>
    <div class="faq-item"><span>Each child completes their own unique clothing item during the week</span><span class="chev">▼</span></div>
    <div class="faq-item"><span>What safety measures are in place?</span><span class="chev">▼</span></div>
  </div>
</section>
<div class="to-top"><svg width="16" height="16" viewBox="0 0 24 24" fill="none" stroke="#fff" stroke-width="3"><path d="M5 15l7-7 7 7"/></svg></div>

<footer class="site-footer">
  <div class="footer-cols">
    <div class="col-brand">
      <div class="brand">Tiny-ThreadDays</div>
      <div class="follow">Follow Us : <i></i><i></i><i></i></div>
    </div>
    <div class="col-links"><h4>Quick Links</h4><ul><li>Home</li><li>About Us</li><li>Camps</li><li>How It Works</li><li>Contact</li></ul></div>
    <div class="col-contact"><h4>Contact Us</h4><ul>
      <li><i></i>Nadelgasse 7, 8004 Zurich, Switzerland</li>
      <li><i></i>Phone: +41 44 555 01 23</li>
      <li><i></i>hello@tiny-threaddays.ch</li></ul></div>
    <div class="col-news"><h4>Subscribe to newsletter</h4><p>Latest updates, exclusive content, and special offers! Subscribe to our newsletter!</p>
      <div class="news-field"><span>Your Email</span><b></b></div></div>
  </div>
  <div class="copyright">© 2025 Tiny-ThreadDays. All Rights Reserved.</div>
</footer>

</body>
</html>
```